Business card design for my company.
I would like the card's background colour to be black. You can also see our web site to get an idea of our brand. https://www.tmwhomecrafting.com.au/
- Name
- Email

```html
<!DOCTYPE html>
<html lang="en">
<head>
<meta charset="utf-8">
<title>TMW Home Crafting – Business Card</title>
<link href="https://fonts.googleapis.com/css2?family=Montserrat:wght@400;500;700&display=swap" rel="stylesheet">
<style>
  :root {
    --card-black: #232323;
    --brand-green: #169443;
    --paper-white: #f4f5f7;
    --backdrop: #e6e6e8;
    --text-light: #f1f1f1;
  }
  * { margin: 0; padding: 0; box-sizing: border-box; }
  html, body {
    width: 1200px; height: 912px; overflow: hidden;
    background: var(--backdrop);
    font-family: "Montserrat", sans-serif;
  }
  .canvas { position: relative; width: 1200px; height: 912px; }
  .card {
    position: absolute; width: 620px; height: 354px;
    background: var(--card-black); border-radius: 18px; overflow: hidden;
    box-shadow: 0 10px 24px rgba(0,0,0,.18);
  }
  .card--front { left: 60px; top: 60px; }
  .card--back { left: 520px; top: 498px; }

  .wordmark {
    display: flex; align-items: center; gap: 12px;
    color: var(--paper-white); font-weight: 700;
    text-transform: uppercase; letter-spacing: 2px;
  }
  .wordmark__square { background: var(--brand-green); flex: none; }
  .card--front .wordmark {
    position: absolute; left: 0; right: 0; top: 148px;
    justify-content: center; font-size: 34px;
  }
  .card--front .wordmark__square { width: 30px; height: 30px; }
  .card--back .wordmark {
    position: absolute; right: 36px; top: 52px; font-size: 20px;
  }
  .card--back .wordmark__square { width: 18px; height: 18px; }

  .person { position: absolute; left: 40px; top: 160px; }
  .person__name {
    color: var(--brand-green); font-weight: 700; font-size: 26px;
    letter-spacing: 1px; text-transform: uppercase; line-height: 1.1;
  }
  .person__role { color: var(--text-light); font-size: 17px; margin-top: 4px; }

  .divider {
    position: absolute; left: 40px; right: 40px; top: 228px;
    height: 1px; background: var(--brand-green);
  }
  .contacts {
    position: absolute; left: 40px; top: 240px; list-style: none;
    color: var(--text-light); font-size: 15px;
  }
  .contacts li { display: flex; align-items: center; gap: 10px; height: 24px; }
  .contacts svg { width: 13px; height: 13px; flex: none; }

  .bottom-bands { position: absolute; left: 0; bottom: 0; width: 620px; height: 44px; }
</style>
</head>
<body>
<div class="canvas">
  <section class="card card--front" aria-label="Card front">
    <div class="wordmark"><span class="wordmark__square"></span>TMW Home Crafting</div>
  </section>

  <section class="card card--back" aria-label="Card back">
    <div class="wordmark"><span class="wordmark__square"></span>TMW Home Crafting</div>

    <div class="person">
      <p class="person__name">Darren Hale</p>
      <p class="person__role">CEO/Founder</p>
    </div>

    <div class="divider"></div>

    <ul class="contacts">
      <li>
        <svg viewBox="0 0 16 16" aria-hidden="true"><path fill="#169443" d="M3.5 1.5l2.5 3-1.5 1.5c.8 1.8 2.2 3.2 4 4L10 8.5l3 2.5-1.5 3C6.5 14 2 9.5 2 3z"/></svg>
        897-555-0142
      </li>
      <li>
        <svg viewBox="0 0 16 16" aria-hidden="true"><rect x="1" y="3" width="14" height="10" fill="none" stroke="#169443" stroke-width="1.6"/><path d="M1 3l7 6 7-6" fill="none" stroke="#169443" stroke-width="1.6"/></svg>
        info@tmwhomecrafting.com.au
      </li>
      <li>
        <svg viewBox="0 0 16 16" aria-hidden="true"><circle cx="8" cy="8" r="6.5" fill="none" stroke="#169443" stroke-width="1.4"/><ellipse cx="8" cy="8" rx="3" ry="6.5" fill="none" stroke="#169443" stroke-width="1.2"/><path d="M1.5 8h13" stroke="#169443" stroke-width="1.2"/></svg>
        www.tmwhomecrafting.com.au
      </li>
    </ul>

    <svg class="bottom-bands" viewBox="0 0 620 44" aria-hidden="true">
      <polygon points="0,34 436,22 426,44 0,44" fill="var(--brand-green)"/>
      <polygon points="446,10 620,2 620,44 432,44" fill="var(--paper-white)"/>
    </svg>
  </section>
</div>
</body>
</html>
```